Product Line Brochure

Would like to have a bifold brochure for our product line to show to customers. Would like it to incorporate the paragraph description of the product line with the picture, followed by the product listings. I would like the brochure to be clean and modern. We are a specialty chemical manufacturer in NJ area.

```html
<!DOCTYPE html>
<html lang="en">
<head>
<meta charset="utf-8">
<title>Architectural Applications – Water, Oil And Stain Repellents</title>
<link rel="stylesheet" href="https://fonts.googleapis.com/css2?family=Encode+Sans+Condensed:wght@600&family=Raleway:wght@400;500;600&display=swap">
<style>
  :root {
    --navy: #1b3a60;
    --navy-dark: #142f50;
    --ink: #3a3a3c;
    --paper: #eff0f2;
    --white: #ffffff;
    --intro-top: #e4e6ec;
    --intro-bottom: #eceef1;
    --photo-light: #9a9cb6;
    --photo-mid: #5d6a82;
    --photo-dark: #2c3a4e;
  }
  * { margin: 0; padding: 0; box-sizing: border-box; }
  html, body { width: 848px; height: 1200px; overflow: hidden; }
  body {
    position: relative;
    font-family: "Raleway", sans-serif;
    font-variant-numeric: lining-nums;
    color: var(--ink);
    background: linear-gradient(160deg, #f6f6f7 0%, var(--paper) 45%, #e7e8eb 100%);
  }
  .nowrap { white-space: nowrap; }
  .page-header {
    position: absolute; left: 0; top: 0; width: 848px; height: 122px;
    background: var(--navy);
    display: flex; align-items: center; justify-content: center;
  }
  .page-title {
    font-family: "Encode Sans Condensed", sans-serif;
    font-weight: 600; font-size: 52px; letter-spacing: 0.5px;
    color: var(--white);
  }
  .hero { position: absolute; left: 0; top: 122px; width: 848px; height: 403px; }
  .hero-intro {
    position: absolute; left: 0; top: 0; width: 403px; height: 403px;
    background: linear-gradient(180deg, var(--intro-top) 0%, var(--intro-bottom) 100%);
  }
  .hero-photo {
    position: absolute; left: 403px; top: 0; width: 445px; height: 403px;
    background: linear-gradient(200deg, var(--photo-light) 0%, var(--photo-mid) 50%, var(--photo-dark) 100%);
  }
  .intro-content { position: absolute; left: 36px; top: 52px; width: 334px; }
  .intro-heading {
    position: relative; padding-left: 22px;
    font-size: 32px; font-weight: 500; line-height: 41px; color: var(--navy);
  }
  .intro-heading::before {
    content: ""; position: absolute; left: 0; top: 4px; width: 11px; height: 62px;
    background: var(--navy);
  }
  .intro-text {
    margin: 8px 0 0 22px;
    font-size: 18.5px; font-weight: 500; line-height: 24px;
    text-align: justify; color: #2e2e30;
  }
  .intro-marks { display: flex; gap: 4px; margin: 11px 0 0 22px; }
  .intro-marks span { width: 13px; height: 13px; background: var(--navy); }
  .listing-title {
    position: absolute; left: 0; top: 550px; width: 848px;
    text-align: center; font-size: 31.5px; font-weight: 500; line-height: 41px; color: var(--ink);
  }
  .product-table { position: absolute; left: 34px; top: 654px; width: 783px; }
  .table-head { position: absolute; left: 0; top: 0; width: 783px; height: 33px; }
  .table-head svg { position: absolute; left: 0; top: 0; }
  .head-cell {
    position: absolute; top: 0; height: 33px; line-height: 33px;
    font-size: 21px; font-weight: 500; color: var(--white);
  }
  .row { position: absolute; left: 0; width: 783px; font-size: 14.6px; font-weight: 500; line-height: 19px; }
  .cell-product { position: absolute; left: 22px; width: 140px; }
  .cell-actives { position: absolute; left: 175px; }
  .cell-voc { position: absolute; left: 376px; width: 18px; text-align: center; }
  .cell-desc { position: absolute; left: 467px; width: 292px; text-align: justify; }
  sup { font-size: 7px; vertical-align: 6px; }
</style>
</head>
<body>
  <header class="page-header">
    <h1 class="page-title">ARCHITECTURAL APPLICATIONS</h1>
  </header>

  <section class="hero">
    <div class="hero-intro">
      <div class="intro-content">
        <h2 class="intro-heading">Water, Oil And Stain Repellents</h2>
        <p class="intro-text">Meridian Polymer, Inc. offers a variety of materials used to impart barrier properties to surfaces such as concrete, grout natural stone, pavers, wood and others. These sealers shield against water, oil, stains as well as corrosion and freeze-thaw damage.</p>
        <div class="intro-marks"><span></span><span></span><span></span></div>
      </div>
    </div>
    <div class="hero-photo" role="img" aria-label="Photograph of an offshore oil platform at sea at dusk"></div>
  </section>

  <h2 class="listing-title">Water, Oil And Stain Repellents<br>Waterborne</h2>

  <section class="product-table">
    <div class="table-head">
      <svg width="783" height="33" viewBox="0 0 783 33" aria-hidden="true">
        <polygon points="10,0 783,0 770,33 0,33" fill="var(--navy-dark)"/>
        <line x1="145" y1="0" x2="145" y2="33" stroke="#ffffff" stroke-width="1.5"/>
        <line x1="316" y1="0" x2="316" y2="33" stroke="#ffffff" stroke-width="1.5"/>
        <line x1="472" y1="0" x2="472" y2="33" stroke="#ffffff" stroke-width="1.5"/>
      </svg>
      <div class="head-cell" style="left:34px">Product</div>
      <div class="head-cell" style="left:172px">Actives (%)</div>
      <div class="head-cell" style="left:341px">VOC (g/L)</div>
      <div class="head-cell" style="left:498px">Description</div>
    </div>

    <div class="row" style="top:57px">
      <div class="cell-product">MPS-254<br>Emulsion</div>
      <div class="cell-actives">36.0</div>
      <div class="cell-desc">General purpose water repellent for various porous hard surfaces. Rapid water beading effect. <span class="nowrap">Non-surface</span> changing</div>
    </div>

    <div class="row" style="top:132px">
      <div class="cell-product">ClearPel<sup>®</sup> 724</div>
      <div class="cell-actives">25.0</div>
      <div class="cell-desc">Short chain fluoropolymer for penetrating water, oil and stain repellency sealers. Exceptional performance on tile, stone and cementitious surfaces. <span class="nowrap">Non-surface</span> changing.</div>
    </div>

    <div class="row" style="top:248px">
      <div class="cell-product">ClearPel<sup>®</sup> 729</div>
      <div class="cell-actives">13.0</div>
      <div class="cell-voc">0</div>
      <div class="cell-desc">Short chain fluoro phosphate ester for penetrating water, oil and stain repellency sealers. Exceptional performance on tile, stone and cementitious surfaces. For brush and roll applications only. <span class="nowrap">Non-surface</span> changing.</div>
    </div>

    <div class="row" style="top:382px">
      <div class="cell-product">MPI-WP6</div>
      <div class="cell-actives">30.0</div>
      <div class="cell-desc">Silicone/fluoro copolymer for penetrating sealers. Exceptional performance on tile, stone and cementitious surfaces. <span class="nowrap">Non-surface</span> changing</div>
    </div>
  </section>
</body>
</html>
```